Revamp Of Landing Page For an Automated AI Voice Agents Agency

here is my current landing page https://app.brightfernpromotionhub.biz/v2/preview/WXKRPmQ4hLzYBvNdTeGS?notrack=true

Please use all my current content and imagery of ai agents in your new design. Make it easy to ready, easy to navigate and easy to understand

I am looking for a SLEEK shiny polished looking website. I like Dark themed sites but am open to see light themed sites too so please dont be shy.

The site should have an Ai Voice Agent Theme about it. Maybe look and feel of futureistic but simple and not intimidating to the average person...

Here are a couple website designs I like for reference:
https://q7v.io/
https://ai-bots.marekholvin.com/
https://chatwelmo.com/ai-agents

Target Market(s)

b2b

Industry/Entity Type

AI Voice Agents

Coding

Coded - Design and coding required

Font styles to use
Other font styles liked:
• open

Requirements
Must have
• all elements and content and images used in existing design.
Nice to have
• open
Should not have
• open

```html
<!DOCTYPE html>
<html lang="en">
<head>
<meta charset="utf-8">
<title>Vocalift — AI Voice Agents</title>
<link rel="stylesheet" href="https://fonts.googleapis.com/css2?family=Outfit:wght@500;600;700;800&family=Montserrat:wght@400;500;600;700&display=swap">
<style>
:root{
  --bg:#111923;
  --bg-deep:#0c121a;
  --ink:#ffffff;
  --muted:#c9ced6;
  --dim:#9aa3ae;
  --violet:#7c3aed;
  --magenta:#d026c9;
  --pink:#e91e8c;
  --orange:#f97316;
  --red:#f0441f;
  --card:#151d2a;
  --line:#2a3342;
}
*{box-sizing:border-box;margin:0;padding:0}
html,body{width:1200px;height:4785px;overflow:hidden;background:var(--bg)}
body{position:relative;font-family:"Montserrat",sans-serif;color:var(--ink)}
.abs{position:absolute}
.brand{font-family:"Outfit",sans-serif;font-weight:600;letter-spacing:3px;color:var(--ink);display:flex;align-items:center;gap:10px}
.brand .dot{width:22px;height:22px;border:2px solid var(--ink);border-radius:50%}
.heading{font-family:"Outfit",sans-serif;font-weight:700;text-transform:uppercase;line-height:1.2}
.gradient-text{background:linear-gradient(90deg,var(--violet),var(--magenta));-webkit-background-clip:text;background-clip:text;color:transparent}
.btn{display:inline-block;padding:0 18px;height:30px;line-height:30px;border-radius:16px;font-size:12px;font-weight:500;color:#fff;background:linear-gradient(90deg,var(--violet),var(--pink))}
.note{font-size:11.5px;line-height:19px;color:var(--muted)}
.note a{color:var(--pink);text-decoration:underline}
.photo{border-radius:4px}
/* hero */
.hero-title{left:141px;top:160px;font-size:38px;line-height:48px}
.hero-sub{left:141px;top:262px;width:380px;font-size:14.5px;line-height:23px;font-weight:600}
.hero-photo{left:666px;top:84px;width:430px;height:430px;border-radius:50%;border:4px solid #e6e9ef;background:radial-gradient(circle at 55% 40%,#3a5d80,#18304a 55%,#0b1624)}
/* workforce */
.section-title{font-size:32px;line-height:38px}
.agent-card{width:290px;height:437px;border:1px solid var(--line);border-radius:8px;overflow:hidden;text-align:center;padding:0 14px}
.agent-card .photo{margin:6px -8px 0;height:175px;background:linear-gradient(160deg,#5a7090,#1d2a3c)}
.agent-card .icon{width:70px;height:70px;border-radius:50%;margin:-38px auto 0;border:3px solid rgba(255,255,255,.6);display:flex;align-items:center;justify-content:center}
.agent-card h3{font-family:"Outfit",sans-serif;font-size:16px;font-weight:500;margin:14px 0 12px}
.agent-card p{font-size:11px;line-height:18px;color:var(--muted)}
.agent-card p b{color:#fff;font-weight:700}
.tint-blue{background:linear-gradient(180deg,var(--card) 40%,#231a52)}
.tint-pink{background:linear-gradient(180deg,var(--card) 40%,#3d1240)}
.tint-green{background:linear-gradient(180deg,var(--card) 40%,#143420)}
.tint-navy{background:linear-gradient(180deg,var(--card) 40%,#142458)}
.tint-gold{background:linear-gradient(180deg,var(--card) 40%,#35301a)}
/* command band */
.command-band{left:0;top:1640px;width:1200px;height:480px;background:radial-gradient(ellipse 60% 45% at 50% 55%,#2d2ad0 0%,#1a1e7a 35%,transparent 75%),radial-gradient(ellipse 40% 20% at 50% 85%,#c35a2a55,transparent)}
.center{left:0;width:1200px;text-align:center}
/* features */
.feature{width:240px;text-align:center}
.feature .ring{width:80px;height:80px;border-radius:50%;margin:0 auto;border:3px solid;display:flex;align-items:center;justify-content:center;background:#0e141c}
.feature h4{font-size:14px;font-weight:600;margin-top:20px;letter-spacing:.5px}
.feature p{font-size:11.5px;line-height:18px;color:var(--dim);margin-top:10px}
/* promise */
.promise-card{border:1px solid var(--line);border-radius:8px;text-align:center}
.promise-card .badge{width:86px;height:86px;border-radius:50%;margin:0 auto;border:3px solid rgba(255,255,255,.7);display:flex;align-items:center;justify-content:center}
.promise-card h4{font-size:15px;font-weight:600;line-height:19px;margin-top:18px}
.promise-card p{font-size:11px;line-height:17px;color:var(--muted);margin-top:6px}
/* faq */
.faq-q{left:650px;width:409px;height:41px;background:#222a38;border-radius:3px;display:flex;align-items:center;padding-left:14px;gap:14px;font-size:14px;font-weight:500}
.faq-q .ring{width:22px;height:22px;border-radius:50%;border:3px solid var(--violet)}
.faq-a{left:704px;width:345px;font-size:11.5px;line-height:20px;color:var(--muted)}
/* footer */
.footer-row{left:141px;width:918px;top:4600px;display:flex;justify-content:space-between;font-size:11px;color:var(--muted)}
.terms-bar{left:141px;top:4630px;width:918px;height:33px;border-radius:17px;background:linear-gradient(90deg,var(--violet),var(--pink));font-size:11px;display:flex;align-items:center;justify-content:center}
</style>
</head>
<body>

<!-- Header -->
<div class="abs brand" style="left:141px;top:24px;font-size:24px"><span class="dot"></span>VOCALIFT</div>

<!-- Hero -->
<h1 class="abs heading hero-title gradient-text">AI Voice Agents<br>That Answer Calls,</h1>
<p class="abs hero-sub">Book Appts, Send Emails, Text Messages, Follow Up Reminders, Transfer Calls &amp; More For You 24 Hours 7 Days A Week!</p>
<a class="abs btn" style="left:141px;top:360px">Get An Instant Free Demo</a>
<p class="abs note" style="left:141px;top:405px;width:370px">We Will Create An Ai Agent Customized For Your Business At No Cost. Simply <a>Click The Button</a> Above And Your Very Own Ai Agent Will Be Calling You In Just A Couple Minutes. Experience The Magic And Get Ready To Be Very Impressed!</p>
<div class="abs hero-photo" role="img" aria-label="Photo of a human-robot agent with headset working at a laptop"></div>

<!-- Workforce -->
<h2 class="abs heading section-title" style="left:141px;top:674px">Meet Your<br>New AI-<br>Powered<br>Workforce</h2>
<a class="abs btn" style="left:141px;top:853px">Get An Instant Free Demo</a>
<p class="abs note" style="left:141px;top:908px;width:255px">We Will Create An Ai Agent Customized For Your Business At No Cost. Simply <a>Click The Button</a> Above And Your Very Own Ai Agent Will Be Calling You In Just A Couple Minutes. Experience The Magic And Get Ready To Be Very Impressed!</p>

<div class="abs agent-card tint-blue" style="left:455px;top:671px">
  <div class="photo" role="img" aria-label="Photo of an AI sales agent with headset at a computer"></div>
  <div class="icon" style="background:linear-gradient(135deg,#6d28d9,#c026d3)"><svg width="30" height="30" viewBox="0 0 24 24" fill="none" stroke="#fff" stroke-width="1.6"><path d="M6 3h4l1 5-3 2a11 11 0 0 0 6 6l2-3 5 1v4a2 2 0 0 1-2 2A17 17 0 0 1 4 5a2 2 0 0 1 2-2z"/></svg></div>
  <h3>Ai Sales Agent</h3>
  <p>Brian will take your inbound sales calls. Will give all detailed information to the customer, answer questions in a normal conversational tone and can book sales appointments or transfer hot prospects to a human to close the sale.</p>
</div>
<div class="abs agent-card tint-pink" style="left:769px;top:671px">
  <div class="photo" role="img" aria-label="Photo of an AI receptionist with headset"></div>
  <div class="icon" style="background:linear-gradient(135deg,#db2777,#f472b6)"><svg width="30" height="30" viewBox="0 0 24 24" fill="none" stroke="#fff" stroke-width="1.6"><path d="M4 5h16v10H9l-4 4V5z"/><path d="M8 10h8"/></svg></div>
  <h3>Ai Receptionist</h3>
  <p><b>Takes Overflow and After Hours Calls or Can Take Calls 24/7 &amp; Transfer To Appropriate Dept.</b><br>Cody handles all your calls 24/7. You can also set him to only take overflow calls and after hours. He can send emails and sms messages and even book appointments over the call</p>
</div>
<div class="abs agent-card tint-green" style="left:141px;top:1135px">
  <div class="photo" role="img" aria-label="Photo of an AI appointment setter with headset"></div>
  <div class="icon" style="background:linear-gradient(135deg,#15803d,#22c55e)"><svg width="30" height="30" viewBox="0 0 24 24" fill="none" stroke="#fff" stroke-width="1.6"><rect x="4" y="5" width="16" height="15" rx="2"/><path d="M4 10h16M9 3v4M15 3v4"/></svg></div>
  <h3>Ai Appointment Setter</h3>
  <p><b>Book Appts &amp; Reservations On Auto Pilot</b><br>Bobby offers business advice, helps brainstorm ideas, and provides insights on growth tactics to support your entrepreneurial journey.</p>
</div>
<div class="abs agent-card tint-navy" style="left:455px;top:1135px">
  <div class="photo" role="img" aria-label="Photo of an AI lead qualifier with headset"></div>
  <div class="icon" style="background:linear-gradient(135deg,#1d4ed8,#3b82f6)"><svg width="30" height="30" viewBox="0 0 24 24" fill="none" stroke="#fff" stroke-width="1.6"><circle cx="12" cy="8" r="4"/><path d="M4 21a8 8 0 0 1 16 0"/></svg></div>
  <h3>Ai Lead Qualifier</h3>
  <p><b>Conversate With Prospects To Qualify Before Handing Over To Sales Team</b><br>All of our ai agents gather information and qualify leads. If they are interested in the services on the call then our ai agents will assist them with booking an appointment with our sales team over the call.</p>
</div>
<div class="abs agent-card tint-gold" style="left:769px;top:1135px">
  <div class="photo" role="img" aria-label="Photo of an AI follow-up assistant with headset"></div>
  <div class="icon" style="background:linear-gradient(135deg,#ea580c,#fbbf24)"><svg width="30" height="30" viewBox="0 0 24 24" fill="none" stroke="#fff" stroke-width="1.6"><path d="M6 16V11a6 6 0 0 1 12 0v5l2 2H4z"/><path d="M10 21h4"/></svg></div>
  <h3>Ai Follow Up Reminders</h3>
  <p><b>Calls, Sends SMS &amp; Email Reminders</b><br>Sam handles all the follow up calls, appt reminders and sends out the email and sms reminders too.</p>
</div>

<!-- Command band -->
<div class="abs command-band" role="img" aria-label="Glowing blue particle wave backdrop"></div>
<p class="abs center" style="top:1768px;font-size:13px;color:var(--red);font-weight:500;letter-spacing:.5px">INSTALL THE POWER OF AI FOR YOUR BUSINESS</p>
<h2 class="abs center heading" style="top:1800px;font-size:31px">Your Wish Is Their Command</h2>
<p class="abs center" style="top:1864px;font-size:14px;font-weight:600">Your New Ai Agents Will Never Call In Sick And Will Never Complain!</p>
<p class="abs" style="left:260px;top:1894px;width:680px;text-align:center;font-size:14px;line-height:24px;font-weight:500">With your new team of AI Agents, handling inbound calls, sending emails and sms messages, booking appointments and handling customer service inquiries is going to save you a ton of time and money.</p>

<!-- Features -->
<h2 class="abs center heading" style="top:2130px;font-size:30px">An Employee That Never Gets Sick!</h2>
<div class="abs feature" style="left:226px;top:2200px">
  <div class="ring" style="border-color:#22c55e"><svg width="40" height="40" viewBox="0 0 24 24" fill="none" stroke="#fff" stroke-width="1.4"><circle cx="12" cy="12" r="7"/><path d="M12 5v14M5 12h14"/></svg></div>
  <h4>TRAINED IN SECONDS</h4><p>Learns Your Entire Website<br>In Seconds</p>
</div>
<div class="abs feature" style="left:480px;top:2200px">
  <div class="ring" style="border-color:#c026d3"><svg width="40" height="40" viewBox="0 0 24 24" fill="none" stroke="#fff" stroke-width="1.4"><circle cx="12" cy="12" r="8"/><path d="M4 12h16M12 4c3 3 3 13 0 16M12 4c-3 3-3 13 0 16"/></svg></div>
  <h4>WORLDWIDE</h4><p>Works Anywhere In<br>The Globe</p>
</div>
<div class="abs feature" style="left:733px;top:2200px">
  <div class="ring" style="border-color:#f97316"><svg width="40" height="40" viewBox="0 0 24 24" fill="none" stroke="#fff" stroke-width="1.4"><circle cx="12" cy="9" r="4"/><path d="M6 20a6 6 0 0 1 12 0"/></svg></div>
  <h4>USER-FRIENDLY</h4><p>Your Ai Agents Sound As If<br>They're Real Humans</p>
</div>

<!-- Ready to hire -->
<h2 class="abs heading" style="left:141px;top:2548px;font-size:31px;line-height:38px">Our AI Agents<br>Our Ready To Be Hired</h2>
<p class="abs" style="left:141px;top:2652px;font-size:14px;font-weight:600;color:var(--orange)">LIGHTNING-FAST RESPONSES</p>
<p class="abs" style="left:141px;top:2676px;width:420px;font-size:20px;line-height:27px;font-weight:500">Instant answers, no coffee, bathroom or lunch breaks needed</p>
<a class="abs btn" style="left:141px;top:2760px">Get An Instant Free Demo</a>
<p class="abs note" style="left:141px;top:2815px;width:370px">We Will Create An Ai Agent Customized For Your Business At No Cost. Simply <a>Click The Button</a> Above And Your Very Own Ai Agent Will Be Calling You In Just A Couple Minutes. Experience The Magic And Get Ready To Be Very Impressed!</p>
<div class="abs" role="img" aria-label="Glowing neon pink and purple lightning bolt illustration" style="left:600px;top:2490px;width:460px;height:455px;background:radial-gradient(ellipse 30% 45% at 55% 45%,#e11d8a,#7c1fb0 45%,transparent 75%),linear-gradient(0deg,#2b1d3d 0,transparent 20%)"></div>

<!-- Promise -->
<div class="abs promise-card" style="left:141px;top:3079px;width:288px;height:342px;background:linear-gradient(180deg,#1b1d2e,#2a1627)">
  <p class="heading" style="margin-top:42px;font-size:22px;line-height:38px">After Our<br>Customers Have<br>A Conversation<br>With Their New AI<br>Voice Agent They<br>Give Us 5 Stars!</p>
  <svg width="180" height="30" viewBox="0 0 180 30" style="margin-top:4px"><g fill="#f97316"><polygon points="15,2 19,11 29,11 21,17 24,27 15,21 6,27 9,17 1,11 11,11"/><polygon transform="translate(36 0)" points="15,2 19,11 29,11 21,17 24,27 15,21 6,27 9,17 1,11 11,11"/><polygon transform="translate(72 0)" points="15,2 19,11 29,11 21,17 24,27 15,21 6,27 9,17 1,11 11,11"/><polygon transform="translate(108 0)" points="15,2 19,11 29,11 21,17 24,27 15,21 6,27 9,17 1,11 11,11"/><polygon transform="translate(144 0)" points="15,2 19,11 29,11 21,17 24,27 15,21 6,27 9,17 1,11 11,11"/></g></svg>
</div>
<h2 class="abs heading" style="left:455px;top:3085px;width:604px;text-align:center;font-size:30px">Our Promise To You:</h2>
<div class="abs promise-card" style="left:455px;top:3172px;width:290px;height:249px;background:linear-gradient(180deg,#121b22,#122a1b);padding-top:38px">
  <div class="badge" style="background:linear-gradient(135deg,#15803d,#22c55e)"><svg width="40" height="40" viewBox="0 0 24 24" fill="none" stroke="#fff" stroke-width="1.6"><rect x="4" y="5" width="16" height="15" rx="2"/><path d="M4 10h16M9 3v4M15 3v4"/></svg></div>
  <h4>14-DAY MONEY-BACK<br>GUARANTEE*</h4>
</div>
<div class="abs promise-card" style="left:769px;top:3172px;width:290px;height:249px;background:linear-gradient(180deg,#121b2a,#142150);padding-top:38px">
  <div class="badge" style="background:linear-gradient(135deg,#1d4ed8,#3b82f6)"><svg width="40" height="40" viewBox="0 0 24 24" fill="none" stroke="#fff" stroke-width="1.6"><circle cx="12" cy="12" r="8"/><path d="M12 7v5l3 2"/></svg></div>
  <h4>24/7 CUSTOMER<br>SUPPORT</h4>
  <p>Often praised for our friendly<br>&amp; helpful support team</p>
</div>

<!-- FAQ -->
<div class="abs" role="img" aria-label="Illustration of a white robot beside a large purple question mark" style="left:141px;top:3567px;width:426px;height:465px;background:radial-gradient(ellipse 35% 40% at 30% 55%,#8b2fd6,transparent 70%),radial-gradient(ellipse 28% 45% at 65% 45%,#b8bcc4,transparent 70%)"></div>
<h2 class="abs heading" style="left:650px;top:3568px;font-size:30px">Do You Have Questions?</h2>
<div class="abs faq-q" style="top:3638px"><span class="ring"></span>What exactly are the AI Voice Agents?</div>
<p class="abs faq-a" style="top:3695px">Ai Voice Agents are specialized human sounding bots, having smart and masterful conversations and each is expertly trained in seconds for a specific business function.</p>
<div class="abs faq-q" style="top:3794px"><span class="ring"></span>How will these AI Voice Agents benefit</div>
<p class="abs faq-a" style="top:3851px">Ai Voice Agents Answer Calls, Book Appts, Send Emails, Text Messages, Follow Up Reminders &amp; More For You 24/7!</p>
<div class="abs faq-q" style="top:3928px"><span class="ring"></span>Are they easy to use?</div>
<p class="abs faq-a" style="top:3985px">We provide a done for you service. We create your AI Voice Agent and launch it within days!</p>

<!-- Closing CTA -->
<div class="abs" style="left:300px;top:4150px;width:600px;height:150px;background:radial-gradient(ellipse 50% 50%,#5b1fa855,transparent 75%)"></div>
<h2 class="abs center heading" style="top:4176px;font-size:31px;line-height:38px">These AI Agents Can Help<br>Your Business Tremendously.<br>Imagine The Possibilities</h2>
<a class="abs btn" style="left:500px;top:4309px">Get An Instant Free Demo</a>
<p class="abs note" style="left:330px;top:4362px;width:540px;text-align:center">We Will Create An Ai Agent Customized For Your Business At No Cost. Simply <a>Click The Button</a> Above And Your Very Own Ai Agent Will Be Calling You In Just A Couple Minutes. Experience The Magic And Get Ready To Be Very Impressed!</p>

<!-- Footer -->
<div class="abs brand" style="left:0;width:1200px;justify-content:center;top:4500px;font-size:36px;letter-spacing:5px"><span class="dot" style="width:34px;height:34px"></span>VOCALIFT</div>
<div class="abs" style="left:141px;top:4567px;width:918px;height:1px;background:var(--line)"></div>
<div class="abs footer-row"><span>© 2025 Vocalift. All rights reserved.</span><span>Disclaimer: Privacy | Terms &amp; Conditions | Earnings &amp; Products Disclaimer</span></div>
<div class="abs terms-bar">*14-Day Money Back Guarantee Terms: If you use the ai agents and you're not happy. Then you can contact us in the first 14 days for a full refund.</div>
<p class="abs center" style="top:4683px;font-size:11px;color:var(--muted)">Do you have questions about ( ) Please email ( )</p>
<p class="abs center" style="top:4736px;font-size:11px;line-height:17px;color:var(--muted)">IMPORTANT: This site is not a part of the FriendStream website or FriendStream Inc. Additionally,<br>this site is NOT endorsed by FriendStream in any way. FRIENDSTREAM is a trademark of FRIENDSTREAM, Inc.</p>

</body>
</html>
```